Talon Microsystems PowerPoint Master Slide Deck Design

This is a 2-phase project to design a slide deck for a semiconductor company in the Silicon Valley. The design budget will be increased with each phase.
The slide deck will need to have one version with a dark background for presentations and a second version with a white background. Otherwise, the slides will be the same. I anticipate we will need a total of 10 slides, but that number may change.
The first phase will be to design a Title and a Title and Content slide.
- The Title Slide is the first slide of the deck. It should include the presentation title, the presenter's name and date of presentation
- The Title and Content slide should include a title and content with bullet points and up to 2 additional sub-bullets
- The Title and Content slide should have a footer that includes the slide #, Talon Microsystems Confidential, and the logo. This footer will be on every slide except the Title Slide
The first two slides will serve as the format for the remaining ~8 slides:
-Header and Content Text (1, 2, 4 column)
-Header and Content Image (bar chart, pie chart, tables)
-Break
-Title only
-Closing (Talon logo only)
Our slides contain a lot of content so a clean and simple design is best.
Both phases will need to include pre-set color options for
-Text and Lines
-Shadows
-Bullets and sub-bullets (including shapes, ex. circle, slash, square, etc.)
-Bar charts, pie charts, tables
Samples of our collateral are attached. Logo files are also attached
Look and feel
Each slider illustrates characteristics of the customer's brand and the style your logo design should communicate.

```html
<!DOCTYPE html>
<html lang="en">
<head>
<meta charset="utf-8">
<title>Talon Microsystems – Master Slide Deck</title>
<link href="https://fonts.googleapis.com/css2?family=Poppins:wght@400;500;600;700&display=swap" rel="stylesheet">
<style>
  :root{
    --blue:#0a55b0;
    --bright:#1f8fff;
    --footer:#0b74b8;
    --page-dot:#2ea3ea;
    --green:#14a58a;
    --bar-blue:#1b5fc0;
    --ink:#3a3a3a;
    --body:#444;
    --paper:#e9f1f9;
    --card:#fff;
    --white:#fff;
  }
  .dark{
    --paper:#000;
    --ink:#fff;
    --heading-accent:var(--bright);
  }
  html,body{margin:0;padding:0;overflow:hidden}
  body{width:790px;height:1200px;background:#fff;position:relative;font-family:"Poppins",sans-serif}
  .slide{position:absolute;width:654px;height:368px;transform-origin:0 0;transform:scale(.5046);overflow:hidden;background:var(--paper)}
  .col-light{left:33px}
  .col-dark{left:428px}
  .row-1{top:18.6px}.row-2{top:213px}.row-3{top:409px}.row-4{top:605px}.row-5{top:802px}.row-6{top:999.5px}
  .layer{position:absolute;inset:0;width:100%;height:100%}

  /* brand name */
  .brand{position:absolute;display:flex;align-items:center;gap:8px;font-weight:500;white-space:nowrap}
  .brand-dot{border-radius:50%;border:3px solid currentColor;box-sizing:border-box}
  .title-brand{right:15px;top:58px;font-size:18px;color:var(--blue)}
  .dark .title-brand{color:var(--white)}
  .title-brand .brand-dot{width:22px;height:22px}

  /* title slide */
  .deck-title{position:absolute;right:15px;top:122px;margin:0;text-align:right;font-size:29px;line-height:34px;font-weight:500;color:var(--ink);letter-spacing:.5px}
  .presenter{position:absolute;right:15px;top:212px;margin:0;font-size:15px;font-weight:700;color:var(--blue)}
  .dark .presenter{color:var(--bright)}
  .date{position:absolute;right:15px;top:240px;margin:0;font-size:11px;font-weight:600;color:var(--ink)}

  /* footer */
  .footer{position:absolute;left:0;right:0;bottom:0;height:32px;background:var(--footer);color:var(--white)}
  .footer .brand{left:8px;top:9px;font-size:10px;gap:4px}
  .footer .brand-dot{width:12px;height:12px;border-width:2px}
  .confidential{position:absolute;right:47px;top:9px;font-size:10.5px;letter-spacing:.3px}
  .page-no{position:absolute;right:10px;top:7px;width:18px;height:18px;border-radius:50%;background:var(--page-dot);font-size:8px;line-height:18px;text-align:center;font-weight:600}

  /* content slides */
  .section-title{position:absolute;margin:0;font-size:28px;line-height:37px;font-weight:500;letter-spacing:1px;color:var(--ink)}
  .card{position:absolute;background:var(--card);box-shadow:0 2px 10px rgba(0,0,0,.18);box-sizing:border-box}
  .text-card{top:103px;width:298px;height:208px;padding:16px 15px;font-size:10px;line-height:19.5px;color:var(--body)}
  .text-card p{margin:0}
  .top-strip{position:absolute;top:0;height:8px;background:var(--blue)}
  .lead{position:absolute;left:290px;top:22px;width:350px;margin:0;font-size:13.3px;line-height:20.5px;color:var(--green)}
  .list-card{top:100px;width:212px;height:221px;padding:10px 11px}
  .list-card h3{margin:0 0 8px;font-size:14px;line-height:19.5px;font-weight:500;color:var(--blue)}
  .ticks{list-style:none;margin:0;padding:0;font-size:10.5px;color:var(--body)}
  .ticks li{position:relative;padding-left:18px;line-height:23px}
  .ticks li::before{content:"";position:absolute;left:2px;top:7px;width:8px;height:4px;border-left:2px solid var(--footer);border-bottom:2px solid var(--footer);transform:rotate(-45deg)}
  .ticks li.sub{padding-left:34px;font-weight:600;color:var(--blue)}
  .ticks li.sub::before{left:18px}

  .break-title{position:absolute;left:0;right:0;top:128px;margin:0;text-align:center;color:var(--white);font-size:26px;line-height:38px;font-weight:500;letter-spacing:.5px}

  .chart-heading{position:absolute;left:327px;top:193px;margin:0;font-size:17.5px;line-height:24px;font-weight:500;letter-spacing:.8px;color:var(--ink)}
  .dark .chart-heading{color:var(--bright)}
  .chart-body{position:absolute;left:331px;top:250px;width:312px;margin:0;font-size:9.3px;line-height:16.6px;color:var(--body)}
  .dark .chart-body{color:var(--white)}
  .axis-label{font-family:"Poppins",sans-serif;font-size:6.5px;fill:#777}
  .dark .axis-label{fill:#bbb}

  .closing-brand{left:0;right:0;top:150px;justify-content:center;gap:14px;font-size:40px;color:var(--white)}
  .closing-brand .brand-dot{width:40px;height:40px;border-width:5px}
</style>
</head>
<body>

<!-- Row 1: Title slide -->
<section class="slide light col-light row-1">
  <svg class="layer" viewBox="0 0 654 368">
    <defs><linearGradient id="photoA" x1="0" y1="0" x2="1" y2="1"><stop offset="0" stop-color="#9fb4d6"/><stop offset=".5" stop-color="#5f86c4"/><stop offset="1" stop-color="#c9d4e4"/></linearGradient></defs>
    <rect width="654" height="368" fill="url(#photoA)" role="img" aria-label="Photo: gloved hand holding a microchip"/>
    <polygon points="458,0 654,0 654,368 460,368 327,183" fill="var(--paper)"/>
    <polygon points="654,281 584,368 654,368" fill="var(--blue)"/>
  </svg>
  <div class="brand title-brand"><span class="brand-dot"></span>Talon Microsystems</div>
  <h1 class="deck-title">NEMO ENIM<br>IPSAM</h1>
  <p class="presenter">Presenter Name Heading</p>
  <p class="date">13 October 2022</p>
</section>
<section class="slide dark col-dark row-1">
  <svg class="layer" viewBox="0 0 654 368">
    <rect width="654" height="368" fill="url(#photoA)" role="img" aria-label="Photo: gloved hand holding a microchip"/>
    <polygon points="458,0 654,0 654,368 460,368 327,183" fill="var(--paper)"/>
    <polygon points="654,281 584,368 654,368" fill="var(--blue)"/>
  </svg>
  <div class="brand title-brand"><span class="brand-dot"></span>Talon Microsystems</div>
  <h1 class="deck-title">NEMO ENIM<br>IPSAM</h1>
  <p class="presenter">Presenter Name Heading</p>
  <p class="date">13 October 2022</p>
</section>

<!-- Row 2: Two column text -->
<section class="slide light col-light row-2">
  <svg class="layer" viewBox="0 0 654 368">
    <defs><linearGradient id="photoB" x1="0" y1="0" x2="1" y2="1"><stop offset="0" stop-color="#1c3a66"/><stop offset=".55" stop-color="#3b3f4a"/><stop offset="1" stop-color="#8a4a22"/></linearGradient></defs>
    <polygon points="377,0 654,0 654,336 475,336" fill="url(#photoB)" role="img" aria-label="Photo: circuit board with processor"/>
  </svg>
  <div class="top-strip" style="left:0;width:215px"></div>
  <h2 class="section-title" style="left:13px;top:20px">QUISQUAM<br>ESTQUI</h2>
  <div class="card text-card" style="left:13px"><p>Sed ut perspiciatis unde omnis iste natus error sit voluptatem accusantium doloremque laudantium, totam rem aperiam, eaque ipsa quae ab illo inventore veritatis et quasi architecto beatae vitae dicta sunt explicabo. Nemo enim ipsam voluptatem quia voluptas sit aspernatur aut odit aut fugit, sed quia consequuntur magni dolores eos qui ratione voluptatem sequi nesciunt. Neque porro quisquam est.</p></div>
  <div class="card text-card" style="left:342px"><p>Sed ut perspiciatis unde omnis iste natus error sit voluptatem accusantium doloremque laudantium, totam rem aperiam, eaque ipsa quae ab illo inventore veritatis et quasi architecto beatae vitae dicta sunt explicabo. Nemo enim ipsam voluptatem quia voluptas sit aspernatur aut odit aut fugit, sed quia consequuntur magni dolores eos qui ratione voluptatem sequi nesciunt. Neque porro quisquam est.</p></div>
  <footer class="footer"><div class="brand"><span class="brand-dot"></span>Talon Microsystems</div><span class="confidential">Talon Microsystems Confidential</span><span class="page-no">2</span></footer>
</section>
<section class="slide dark col-dark row-2">
  <svg class="layer" viewBox="0 0 654 368">
    <polygon points="377,0 654,0 654,336 475,336" fill="url(#photoB)" role="img" aria-label="Photo: circuit board with processor"/>
  </svg>
  <div class="top-strip" style="left:0;width:215px"></div>
  <h2 class="section-title" style="left:13px;top:20px">QUISQUAM<br>ESTQUI</h2>
  <div class="card text-card" style="left:13px"><p>Sed ut perspiciatis unde omnis iste natus error sit voluptatem accusantium doloremque laudantium, totam rem aperiam, eaque ipsa quae ab illo inventore veritatis et quasi architecto beatae vitae dicta sunt explicabo. Nemo enim ipsam voluptatem quia voluptas sit aspernatur aut odit aut fugit, sed quia consequuntur magni dolores eos qui ratione voluptatem sequi nesciunt. Neque porro quisquam est.</p></div>
  <div class="card text-card" style="left:342px"><p>Sed ut perspiciatis unde omnis iste natus error sit voluptatem accusantium doloremque laudantium, totam rem aperiam, eaque ipsa quae ab illo inventore veritatis et quasi architecto beatae vitae dicta sunt explicabo. Nemo enim ipsam voluptatem quia voluptas sit aspernatur aut odit aut fugit, sed quia consequuntur magni dolores eos qui ratione voluptatem sequi nesciunt. Neque porro quisquam est.</p></div>
  <footer class="footer"><div class="brand"><span class="brand-dot"></span>Talon Microsystems</div><span class="confidential">Talon Microsystems Confidential</span><span class="page-no">2</span></footer>
</section>

<!-- Row 3: Bullet columns -->
<section class="slide light col-light row-3">
  <svg class="layer" viewBox="0 0 654 368">
    <defs><linearGradient id="photoC" x1="0" y1="0" x2="1" y2="1"><stop offset="0" stop-color="#2a2f4a"/><stop offset="1" stop-color="#15182a"/></linearGradient></defs>
    <rect width="654" height="368" fill="url(#photoC)" role="img" aria-label="Photo: hand holding a processor chip"/>
    <polygon points="225,0 654,0 654,336 400,336" fill="var(--paper)"/>
    <polygon points="654,300 615,336 654,336" fill="var(--blue)"/>
  </svg>
  <div class="top-strip" style="left:375px;right:0"></div>
  <p class="lead">Nemo enim ipsam voluptatem quia voluptas sit aspernatur aut odit aut fugit, sed quia consequ untur magni dolores.</p>
  <h2 class="section-title" style="left:18px;top:143px;color:var(--white)">QUISQUAM<br>ESTQUI</h2>
  <div class="card list-card" style="left:204px"><h3>Quis autem vel eum iure reprehenderit</h3><ul class="ticks"><li>Sed ut perspiciatis unde omnis</li><li>Iste natus error sit voluptatem</li><li class="sub">Accusantium doloremque</li><li class="sub">Laudantium, totam</li><li>Rem aperiam</li><li>Sed ut perspiciatis unde</li></ul></div>
  <div class="card list-card" style="left:428px"><h3>Quis autem vel eum iure reprehenderit</h3><ul class="ticks"><li>Sed ut perspiciatis unde omnis</li><li>Iste natus error sit voluptatem</li><li>Sed ut perspiciatis unde omnis</li><li>Iste natus error sit voluptatem</li><li>Rem aperiam</li><li>Sed ut perspiciatis unde</li></ul></div>
  <footer class="footer"><div class="brand"><span class="brand-dot"></span>Talon Microsystems</div><span class="confidential">Talon Microsystems Confidential</span><span class="page-no">3</span></footer>
</section>
<section class="slide dark col-dark row-3">
  <svg class="layer" viewBox="0 0 654 368">
    <rect width="654" height="368" fill="url(#photoC)" role="img" aria-label="Photo: hand holding a processor chip"/>
    <polygon points="225,0 654,0 654,336 400,336" fill="var(--paper)"/>
    <polygon points="654,300 615,336 654,336" fill="var(--blue)"/>
  </svg>
  <div class="top-strip" style="left:375px;right:0"></div>
  <p class="lead">Nemo enim ipsam voluptatem quia voluptas sit aspernatur aut odit aut fugit, sed quia consequ untur magni dolores.</p>
  <h2 class="section-title" style="left:18px;top:143px;color:var(--white)">QUISQUAM<br>ESTQUI</h2>
  <div class="card list-card" style="left:204px"><h3>Quis autem vel eum iure reprehenderit</h3><ul class="ticks"><li>Sed ut perspiciatis unde omnis</li><li>Iste natus error sit voluptatem</li><li class="sub">Accusantium doloremque</li><li class="sub">Laudantium, totam</li><li>Rem aperiam</li><li>Sed ut perspiciatis unde</li></ul></div>
  <div class="card list-card" style="left:428px"><h3>Quis autem vel eum iure reprehenderit</h3><ul class="ticks"><li>Sed ut perspiciatis unde omnis</li><li>Iste natus error sit voluptatem</li><li>Sed ut perspiciatis unde omnis</li><li>Iste natus error sit voluptatem</li><li>Rem aperiam</li><li>Sed ut perspiciatis unde</li></ul></div>
  <footer class="footer"><div class="brand"><span class="brand-dot"></span>Talon Microsystems</div><span class="confidential">Talon Microsystems Confidential</span><span class="page-no">3</span></footer>
</section>

<!-- Row 4: Break -->
<section class="slide light col-light row-4">
  <svg class="layer" viewBox="0 0 654 368">
    <defs><linearGradient id="photoD" x1="0" y1="0" x2="1" y2="1"><stop offset="0" stop-color="#169a8c"/><stop offset=".6" stop-color="#0d6aa6"/><stop offset="1" stop-color="#0a4fa6"/></linearGradient></defs>
    <rect width="654" height="368" fill="url(#photoD)" role="img" aria-label="Photo: circuit board with teal and blue tint"/>
  </svg>
  <h2 class="break-title">NEQUE PORRO QUISQUAM EST<br>QUI DOLOREM IPSUM</h2>
  <footer class="footer"><div class="brand"><span class="brand-dot"></span>Talon Microsystems</div><span class="confidential">Talon Microsystems Confidential</span><span class="page-no">4</span></footer>
</section>
<section class="slide dark col-dark row-4">
  <svg class="layer" viewBox="0 0 654 368">
    <rect width="654" height="368" fill="url(#photoD)" role="img" aria-label="Photo: circuit board with teal and blue tint"/>
  </svg>
  <h2 class="break-title">NEQUE PORRO QUISQUAM EST<br>QUI DOLOREM IPSUM</h2>
  <footer class="footer"><div class="brand"><span class="brand-dot"></span>Talon Microsystems</div><span class="confidential">Talon Microsystems Confidential</span><span class="page-no">4</span></footer>
</section>

<!-- Row 5: Chart and image -->
<section class="slide light col-light row-5">
  <svg class="layer" viewBox="0 0 654 368">
    <defs><linearGradient id="photoE" x1="0" y1="0" x2="1" y2="1"><stop offset="0" stop-color="#3a4a78"/><stop offset=".5" stop-color="#1f6fb0"/><stop offset="1" stop-color="#8fd0ee"/></linearGradient></defs>
    <rect x="327" y="20" width="318" height="163" fill="url(#photoE)" role="img" aria-label="Photo: technician in cleanroom suit at a microscope"/>
    <g class="chart">
      <line x1="31" y1="38" x2="31" y2="308" stroke="#999" stroke-width=".6"/>
      <line x1="31" y1="308" x2="310" y2="308" stroke="#999" stroke-width=".6"/>
      <g class="axis-label" text-anchor="end">
        <text x="28" y="43">100%</text><text x="28" y="70">90%</text><text x="28" y="96">80%</text><text x="28" y="123">70%</text><text x="28" y="150">60%</text><text x="28" y="176">50%</text><text x="28" y="203">40%</text><text x="28" y="230">30%</text><text x="28" y="256">20%</text><text x="28" y="283">10%</text><text x="28" y="310">0%</text>
      </g>
      <g fill="var(--green)"><rect x="41" y="164" width="12" height="144"/><rect x="81" y="185" width="12" height="123"/><rect x="120" y="108" width="12" height="200"/><rect x="160" y="191" width="12" height="117"/><rect x="200" y="236" width="12" height="72"/><rect x="239" y="140" width="12" height="168"/><rect x="279" y="89" width="12" height="219"/></g>
      <g fill="var(--bar-blue)"><rect x="53" y="220" width="12" height="88"/><rect x="93" y="126" width="12" height="182"/><rect x="132" y="255" width="12" height="53"/><rect x="172" y="217" width="12" height="91"/><rect x="212" y="199" width="12" height="109"/><rect x="251" y="164" width="12" height="144"/><rect x="291" y="284" width="12" height="24"/></g>
      <g class="axis-label" text-anchor="middle"><text x="53" y="321">2015</text><text x="93" y="321">2016</text><text x="132" y="321">2017</text><text x="172" y="321">2018</text><text x="212" y="321">2019</text><text x="251" y="321">2020</text><text x="291" y="321">2022</text></g>
    </g>
  </svg>
  <h2 class="chart-heading">EXCEPTEUR SINT OCCAECAT<br>CUPIDATATNON</h2>
  <p class="chart-body">Sed ut perspiciatis unde omnis iste natus error sit voluptatem accusantium doloremque laudantium, totam rem aperiam, eaque ipsa quae ab illo inventore veritatis et quasi architecto beatae vitae dicta sunt explicabo.</p>
  <footer class="footer"><div class="brand"><span class="brand-dot"></span>Talon Microsystems</div><span class="confidential">Talon Microsystems Confidential</span><span class="page-no">5</span></footer>
</section>
<section class="slide dark col-dark row-5">
  <svg class="layer" viewBox="0 0 654 368">
    <rect x="327" y="20" width="318" height="163" fill="url(#photoE)" role="img" aria-label="Photo: technician in cleanroom suit at a microscope"/>
    <g class="chart">
      <line x1="31" y1="38" x2="31" y2="308" stroke="#777" stroke-width=".6"/>
      <line x1="31" y1="308" x2="310" y2="308" stroke="#777" stroke-width=".6"/>
      <g class="axis-label" text-anchor="end">
        <text x="28" y="43">100%</text><text x="28" y="70">90%</text><text x="28" y="96">80%</text><text x="28" y="123">70%</text><text x="28" y="150">60%</text><text x="28" y="176">50%</text><text x="28" y="203">40%</text><text x="28" y="230">30%</text><text x="28" y="256">20%</text><text x="28" y="283">10%</text><text x="28" y="310">0%</text>
      </g>
      <g fill="var(--green)"><rect x="41" y="164" width="12" height="144"/><rect x="81" y="185" width="12" height="123"/><rect x="120" y="108" width="12" height="200"/><rect x="160" y="191" width="12" height="117"/><rect x="200" y="236" width="12" height="72"/><rect x="239" y="140" width="12" height="168"/><rect x="279" y="89" width="12" height="219"/></g>
      <g fill="var(--bar-blue)"><rect x="53" y="220" width="12" height="88"/><rect x="93" y="126" width="12" height="182"/><rect x="132" y="255" width="12" height="53"/><rect x="172" y="217" width="12" height="91"/><rect x="212" y="199" width="12" height="109"/><rect x="251" y="164" width="12" height="144"/><rect x="291" y="284" width="12" height="24"/></g>
      <g class="axis-label" text-anchor="middle"><text x="53" y="321">2015</text><text x="93" y="321">2016</text><text x="132" y="321">2017</text><text x="172" y="321">2018</text><text x="212" y="321">2019</text><text x="251" y="321">2020</text><text x="291" y="321">2022</text></g>
    </g>
  </svg>
  <h2 class="chart-heading">EXCEPTEUR SINT OCCAECAT<br>CUPIDATATNON</h2>
  <p class="chart-body">Sed ut perspiciatis unde omnis iste natus error sit voluptatem accusantium doloremque laudantium, totam rem aperiam, eaque ipsa quae ab illo inventore veritatis et quasi architecto beatae vitae dicta sunt explicabo.</p>
  <footer class="footer"><div class="brand"><span class="brand-dot"></span>Talon Microsystems</div><span class="confidential">Talon Microsystems Confidential</span><span class="page-no">5</span></footer>
</section>

<!-- Row 6: Closing -->
<section class="slide light col-light row-6">
  <svg class="layer" viewBox="0 0 654 368">
    <defs><radialGradient id="photoF" cx=".5" cy=".5" r=".7"><stop offset="0" stop-color="#1a6ff0"/><stop offset="1" stop-color="#0a4fe8"/></radialGradient></defs>
    <rect width="654" height="368" fill="url(#photoF)" role="img" aria-label="Background image: blue circuit-board texture"/>
  </svg>
  <div class="brand closing-brand"><span class="brand-dot"></span>Talon Microsystems</div>
</section>
<section class="slide dark col-dark row-6">
  <svg class="layer" viewBox="0 0 654 368">
    <rect width="654" height="368" fill="url(#photoF)" role="img" aria-label="Background image: blue circuit-board texture"/>
  </svg>
  <div class="brand closing-brand"><span class="brand-dot"></span>Talon Microsystems</div>
</section>

</body>
</html>
```